Structural Engineering Business Card

Brookvane Drafting does residential house plans for clients in Central Florida. Would like simple but elegant business card that is appropriate for a house plan engineering company. Prefer black business card with black/white them but open to other shades of blue. I uploaded a sample card that I came across that looked good but please come up with your own creative designs.

Contact Information for Business Card

Name, Title, Phone, Email, Address, website

```html
<!DOCTYPE html>
<html lang="en">
<head>
<meta charset="utf-8">
<title>Brookvane Drafting – Business Card</title>
<link rel="stylesheet" href="https://fonts.googleapis.com/css2?family=Arimo:wght@400;700&display=swap">
<style>
  :root {
    --page-bg: #d6d6d6;
    --card-bg: #222222;
    --card-back-bg: #1d1d1d;
    --ink-light: #ffffff;
    --ink-muted: #e6e6e6;
    --rule: #bdbdbd;
    --back-mark: #3a3a3a;
  }
  * { box-sizing: border-box; margin: 0; padding: 0; }
  html, body {
    width: 1200px; height: 788px; overflow: hidden;
    background: var(--page-bg);
    font-family: "Arimo", Arial, sans-serif;
  }
  .stage {
    width: 1200px; height: 788px;
    display: flex; align-items: center; justify-content: center; gap: 40px;
  }
  .card {
    position: relative;
    width: 520px; height: 297px;
    border-radius: 22px;
    background: var(--card-bg);
    color: var(--ink-light);
    overflow: hidden;
  }
  .card--back { background: var(--card-back-bg); }

  .brand {
    position: absolute; top: 52px; left: 0; right: 0;
    display: flex; align-items: center; justify-content: center; gap: 12px;
    font-weight: 700; font-size: 30px; letter-spacing: 0.5px;
    text-transform: uppercase;
  }
  .brand-square { width: 20px; height: 20px; background: var(--ink-light); }

  .rule-main {
    position: absolute; top: 128px; left: 36px; right: 36px;
    height: 1px; background: var(--rule);
  }

  .person { position: absolute; left: 36px; top: 150px; }
  .person-name { font-weight: 700; font-size: 19px; letter-spacing: 0.4px; text-transform: uppercase; }
  .person-title { font-size: 15px; color: var(--ink-muted); margin-top: 2px; }
  .rule-short { width: 200px; height: 1px; background: var(--rule); margin: 12px 0 10px; }

  .contact-list { list-style: none; font-size: 14px; line-height: 21px; color: var(--ink-muted); }
  .contact-list li { display: flex; align-items: center; gap: 8px; }
  .contact-list svg { width: 12px; height: 12px; flex: none; fill: var(--ink-light); }

  .rule-vertical {
    position: absolute; left: 300px; top: 160px;
    width: 1px; height: 100px; background: var(--rule);
  }
  .address {
    position: absolute; left: 322px; top: 160px;
    font-size: 14px; line-height: 21px; color: var(--ink-muted);
    font-style: normal;
  }

  .back-brand {
    position: absolute; inset: 0;
    display: flex; align-items: center; justify-content: center;
    font-weight: 700; font-size: 42px; text-transform: uppercase;
    color: var(--back-mark); letter-spacing: 0.5px;
  }
</style>
</head>
<body>
  <main class="stage">
    <section class="card card--front" aria-label="Business card front">
      <div class="brand"><span class="brand-square"></span><span>Brookvane Drafting</span></div>
      <div class="rule-main"></div>
      <div class="person">
        <p class="person-name">Marcus Hale</p>
        <p class="person-title">Founder/CEO</p>
        <div class="rule-short"></div>
        <ul class="contact-list">
          <li>
            <svg viewBox="0 0 24 24" aria-hidden="true"><path d="M6.6 10.8a15 15 0 0 0 6.6 6.6l2.2-2.2c.3-.3.7-.4 1-.2 1.1.4 2.3.6 3.6.6.6 0 1 .4 1 1V20c0 .6-.4 1-1 1A17 17 0 0 1 3 4c0-.6.4-1 1-1h3.5c.6 0 1 .4 1 1 0 1.3.2 2.5.6 3.6.1.3 0 .7-.2 1z"/></svg>
            407.555.0182
          </li>
          <li>
            <svg viewBox="0 0 24 24" aria-hidden="true"><path d="M2 5h20v14H2z M2 5l10 8 10-8" fill="none" stroke="#fff" stroke-width="2"/></svg>
            info@brookvanedrafting.com
          </li>
          <li>
            <svg viewBox="0 0 24 24" aria-hidden="true"><circle cx="12" cy="12" r="10"/></svg>
            www.brookvanedrafting.com
          </li>
        </ul>
      </div>
      <div class="rule-vertical"></div>
      <address class="address">1290 Lakeview Dr Suite 140<br>Winter Park, FL 32789</address>
    </section>

    <section class="card card--back" aria-label="Business card back">
      <div class="back-brand">Brookvane Drafting</div>
    </section>
  </main>
</body>
</html>
```